Harborline Renewal Business Card Design

Professional and clean design. The design colors should flow with the logo. Two-sided card with the website on the back which is:

www.HarborlineRenewal.example.

"Specializing in Water Damage Restoration"

On the front I need the name, email, phone, and logo.

Name: Darnell Quisby
Email: Darnell@HarborlineRenewal.example
Phone: 555-318-2046 for now

I only have the Preview and Thumbnail right now but should have the source files uploaded within a day or two.

Target Market(s)

Flood victims, home owners with water damage from busted pipes etc...

Industry/Entity Type

Business

Contact Information for Business Card

Name: Darnell Quisby

Font styles to use
Serif
Sans Serif

Requirements
Must have
• Business Card Details Info

```html
<!DOCTYPE html>
<html lang="en">
<head>
<meta charset="utf-8">
<title>Harborline Renewal – Business Card</title>
<link rel="stylesheet" href="https://fonts.googleapis.com/css2?family=Crimson+Pro:ital,wght@0,600;1,700&family=Fira+Sans+Condensed:ital,wght@0,500;1,500&display=swap">
<style>
  :root {
    --sky: #5bbfea;
    --ocean: #2f96d2;
    --slate: #555555;
    --paper: #ececec;
    --ink-light: #ffffff;
  }
  html, body {
    margin: 0;
    padding: 0;
    width: 960px;
    height: 1200px;
    overflow: hidden;
    background: var(--paper);
  }
  .canvas {
    position: relative;
    width: 960px;
    height: 1200px;
  }
  .card {
    position: absolute;
    left: 101px;
    width: 761px;
    height: 444px;
    overflow: hidden;
    box-shadow: 0 10px 18px rgba(0,0,0,0.25);
  }
  .card--front { top: 82px; }
  .card--back { top: 658px; }
  .card__art {
    position: absolute;
    inset: 0;
    width: 761px;
    height: 444px;
  }
  .holder-name {
    position: absolute;
    left: 51px;
    top: 108px;
    margin: 0;
    font-family: "Crimson Pro", Georgia, serif;
    font-style: italic;
    font-weight: 700;
    font-size: 33px;
    letter-spacing: 1px;
    color: var(--ink-light);
    text-transform: uppercase;
  }
  .contact-list {
    position: absolute;
    left: 50px;
    top: 0;
    margin: 0;
    padding: 0;
    list-style: none;
  }
  .contact-item {
    position: absolute;
    left: 0;
    display: flex;
    align-items: center;
    width: 500px;
    height: 36px;
    font-family: "Fira Sans Condensed", "Arial Narrow", sans-serif;
    font-style: italic;
    font-weight: 500;
    font-size: 16.5px;
    color: var(--ink-light);
    white-space: nowrap;
  }
  .contact-item--phone { top: 170px; }
  .contact-item--email { top: 259px; }
  .contact-item--web { top: 337px; }
  .contact-item__icon {
    width: 38px;
    height: 36px;
    margin-right: 24px;
    flex: none;
  }
  .brand {
    position: absolute;
    left: 411px;
    top: 0;
    width: 320px;
    height: 444px;
  }
  .brand__dot {
    position: absolute;
    left: 100px;
    top: 176px;
    width: 120px;
    height: 120px;
    border-radius: 50%;
    background: var(--ocean);
  }
  .brand__name {
    position: absolute;
    left: 0;
    top: 326px;
    width: 320px;
    margin: 0;
    text-align: center;
    font-family: "Crimson Pro", Georgia, serif;
    font-weight: 600;
    font-size: 25px;
    letter-spacing: 1.5px;
    text-transform: uppercase;
    color: var(--ocean);
  }
  .back-url {
    position: absolute;
    left: 0;
    top: 158px;
    width: 761px;
    margin: 0;
    text-align: center;
    font-family: "Fira Sans Condensed", "Arial Narrow", sans-serif;
    font-weight: 500;
    font-size: 29px;
    color: var(--sky);
  }
  .back-dot {
    position: absolute;
    left: 595px;
    top: 251px;
    width: 126px;
    height: 126px;
    border-radius: 50%;
    background: var(--ocean);
  }
</style>
</head>
<body>
<main class="canvas">

  <section class="card card--front" aria-label="Business card front">
    <svg class="card__art" viewBox="0 0 761 444" aria-hidden="true">
      <rect width="761" height="444" fill="var(--sky)"/>
      <path d="M0,27 C250,28 540,90 761,214 L761,444 L0,444 Z" fill="var(--ocean)"/>
      <path d="M0,45 C260,46 540,106 761,224 L761,444 L0,444 Z" fill="var(--slate)"/>
      <rect x="0" y="390" width="761" height="19" fill="var(--sky)"/>
    </svg>

    <h1 class="holder-name">Darnell Quisby</h1>

    <ul class="contact-list">
      <li class="contact-item contact-item--phone">
        <svg class="contact-item__icon" viewBox="0 0 38 36" aria-hidden="true">
          <path d="M6,4 C3,6 2,10 4,15 C8,24 16,31 26,34 C30,35 33,33 35,30 L29,24 C27,23 25,24 24,26 C18,24 13,18 11,13 C13,12 14,10 13,8 Z" fill="var(--ocean)"/>
        </svg>
        <span>555-318-2046</span>
      </li>
      <li class="contact-item contact-item--email">
        <svg class="contact-item__icon" viewBox="0 0 38 36" aria-hidden="true">
          <rect x="2" y="6" width="33" height="24" fill="var(--ocean)"/>
          <path d="M2,6 L18.5,20 L35,6 M2,30 L14,17 M35,30 L23,17" stroke="var(--slate)" stroke-width="1.4" fill="none"/>
        </svg>
        <span>Darnell@HarborlineRenewal.example</span>
      </li>
      <li class="contact-item contact-item--web">
        <svg class="contact-item__icon" viewBox="0 0 38 36" aria-hidden="true">
          <g fill="none" stroke="var(--ocean)" stroke-width="2">
            <circle cx="19" cy="18" r="16"/>
            <ellipse cx="19" cy="18" rx="7" ry="16"/>
            <path d="M19,2 V34 M3,18 H35 M6,10 H32 M6,26 H32"/>
          </g>
        </svg>
        <span>www.HarborlineRenewal.example</span>
      </li>
    </ul>

    <div class="brand">
      <span class="brand__dot" aria-hidden="true"></span>
      <p class="brand__name">Harborline Renewal</p>
    </div>
  </section>

  <section class="card card--back" aria-label="Business card back">
    <svg class="card__art" viewBox="0 0 761 444" aria-hidden="true">
      <rect width="761" height="444" fill="var(--slate)"/>
      <path d="M0,252 C120,236 250,258 400,318 C560,382 680,418 761,398 L761,444 L0,444 Z" fill="var(--ocean)"/>
      <path d="M0,300 C150,282 300,308 430,350 C570,394 680,428 761,412 L761,444 L0,444 Z" fill="var(--sky)"/>
    </svg>
    <p class="back-url">www.HarborlineRenewal.example</p>
    <span class="back-dot" aria-hidden="true"></span>
  </section>

</main>
</body>
</html>
```